Tolbek cards

I want a simple business card that pops.
Logo on one side.
On side two i want.
"Are you thinking about a new building on your property, or renovating an existing structure? Contact".....
Owners Name: Dale Whitacre
Owners Phone number: 610-555-0187
Address:4076 Copper Ridge RD, Millbrook, PA 16901
Committed to Quality, Service, and Integrity

```html
<!DOCTYPE html>
<html lang="en">
<head>
<meta charset="utf-8">
<title>Tolbek Builders LLC – Business Cards</title>
<link rel="stylesheet" href="https://fonts.googleapis.com/css2?family=Poppins:wght@400;500;700&display=swap">
<style>
  :root {
    --page-bg: #232323;
    --card-black: #151515;
    --card-back: #171717;
    --emboss-grey: #3b3b3b;
    --brown-band: #402c1c;
    --bronze: #a98463;
    --deco-dark: #0e0e0e;
    --text-light: #ffffff;
  }
  * { box-sizing: border-box; margin: 0; padding: 0; }
  html, body {
    width: 1200px; height: 800px; overflow: hidden;
    background: var(--page-bg);
    font-family: "Poppins", sans-serif;
  }
  .sheet { position: relative; width: 1200px; height: 800px; }
  .card {
    position: absolute; left: 320px; width: 560px; height: 320px;
    border-radius: 26px; overflow: hidden;
  }
  /* Back side */
  .card--back { top: 50px; background: var(--card-back); }
  .back-logo {
    position: absolute; inset: 0;
    display: flex; flex-direction: column; align-items: center; justify-content: center;
    color: var(--emboss-grey); font-weight: 700; text-align: center;
  }
  .back-logo__name { font-size: 64px; line-height: 1; letter-spacing: 2px; text-transform: uppercase; }
  .back-logo__sub { font-size: 22px; letter-spacing: 3px; margin-top: 6px; text-transform: uppercase; }

  /* Front side */
  .card--front { top: 430px; background: var(--card-black); color: var(--text-light); }
  .front-band {
    position: absolute; left: 0; right: 0; bottom: 0; height: 150px;
    background: var(--brown-band);
  }
  .front-deco {
    position: absolute; right: 0; bottom: 0; width: 150px; height: 190px;
    background: var(--deco-dark);
  }
  .front-logo {
    position: absolute; left: 34px; top: 36px;
    color: var(--bronze); font-weight: 700; text-transform: uppercase; line-height: 1;
  }
  .front-logo__name { font-size: 34px; letter-spacing: 1px; }
  .front-logo__sub { font-size: 12px; letter-spacing: 2px; margin-top: 4px; }
  .front-quote {
    position: absolute; right: 30px; top: 34px; width: 260px;
    font-size: 12px; line-height: 1.45; text-align: right;
  }
  .owner { position: absolute; left: 34px; top: 150px; }
  .owner__name { font-size: 26px; font-weight: 700; line-height: 1.1; }
  .owner__role { font-size: 13px; font-weight: 500; margin-top: 2px; }
  .owner__tagline { font-size: 12px; line-height: 1.35; margin-top: 6px; }
  .contact { list-style: none; margin-top: 6px; font-size: 12px; }
  .contact__item { display: flex; align-items: center; gap: 8px; margin-top: 4px; }
  .contact__icon {
    width: 16px; height: 16px; border-radius: 50%; background: var(--text-light);
    display: inline-flex; align-items: center; justify-content: center; flex: none;
  }
</style>
</head>
<body>
<main class="sheet">
  <section class="card card--back" aria-label="Card back">
    <div class="back-logo">
      <span class="back-logo__name">Tolbek</span>
      <span class="back-logo__sub">Builders LLC</span>
    </div>
  </section>

  <section class="card card--front" aria-label="Card front">
    <div class="front-band"></div>
    <div class="front-deco" role="img" aria-label="Large dark brand decoration"></div>

    <div class="front-logo">
      <div class="front-logo__name">Tolbek</div>
      <div class="front-logo__sub">Builders LLC</div>
    </div>

    <p class="front-quote">"Are you thinking about a new building on your property, or renovating an existing structure? Contact" .....</p>

    <div class="owner">
      <h1 class="owner__name">Dale Whitacre</h1>
      <p class="owner__role">Owners</p>
      <p class="owner__tagline">Committed to Quality,<br>Service, and Integrity</p>
      <ul class="contact">
        <li class="contact__item">
          <span class="contact__icon">
            <svg width="10" height="10" viewBox="0 0 24 24" aria-hidden="true"><path fill="#402c1c" d="M6.6 10.8a15.1 15.1 0 0 0 6.6 6.6l2.2-2.2c.3-.3.7-.4 1-.2 1.1.4 2.3.6 3.6.6.6 0 1 .4 1 1V20c0 .6-.4 1-1 1A17 17 0 0 1 3 4c0-.6.4-1 1-1h3.5c.6 0 1 .4 1 1 0 1.3.2 2.5.6 3.6.1.3 0 .7-.2 1z"/></svg>
          </span>
          610-555-0187
        </li>
        <li class="contact__item">
          <span class="contact__icon">
            <svg width="10" height="10" viewBox="0 0 24 24" aria-hidden="true"><path fill="#402c1c" d="M12 2a7 7 0 0 0-7 7c0 5.2 7 13 7 13s7-7.8 7-13a7 7 0 0 0-7-7zm0 9.5a2.5 2.5 0 1 1 0-5 2.5 2.5 0 0 1 0 5z"/></svg>
          </span>
          4076 Copper Ridge RD, Millbrook, PA 16901
        </li>
      </ul>
    </div>
  </section>
</main>
</body>
</html>
```